Moravel Aesthetic Doctor

I require an elegant, luxurious looking business card for my aesthetic business. I am a doctor and that will set me aside from competitors. I am planning to provide home and spa based treatments to clients with high expectations. I have attached my logo.

```html
<!DOCTYPE html>
<html lang="en">
<head>
<meta charset="utf-8">
<title>Moravel Aesthetic Doctor – Business Card</title>
<link href="https://fonts.googleapis.com/css2?family=Roboto:wght@300;400;500&display=swap" rel="stylesheet">
<style>
  :root {
    --backdrop: #c9c9c9;
    --card-white: #ffffff;
    --brand-blue: #3497d6;
    --accent-blue: #5bbfea;
    --text-grey: #8c8c8c;
    --logo-grey: #8a8a8a;
    --soft-blue-a: #e6f1fb;
    --soft-blue-b: #f5f9fe;
  }
  * { box-sizing: border-box; margin: 0; padding: 0; }
  html, body {
    width: 1125px; height: 1200px; overflow: hidden;
    background: var(--backdrop);
    font-family: "Roboto", Arial, sans-serif;
  }
  .canvas { position: relative; width: 1125px; height: 1200px; }
  .card {
    position: absolute; left: 151px; width: 824px; height: 472px;
    border-radius: 26px; overflow: hidden;
    background: var(--card-white);
    box-shadow: 0 3px 5px rgba(0,0,0,.35);
  }
  .card--front { top: 98px; }
  .card--back { top: 631px; background: var(--brand-blue); }
  .card svg.art { position: absolute; inset: 0; }

  .wordmark { position: absolute; font-weight: 400; line-height: 1; }
  .wordmark__name { display: block; font-size: 54px; letter-spacing: 2px; }
  .wordmark__tag { display: block; font-size: 23px; letter-spacing: 1.5px; margin-top: 8px; }
  .card--front .wordmark { left: 48px; top: 42px; color: var(--logo-grey); }
  .card--back .wordmark { left: 548px; top: 52px; color: #fff; text-align: center; }

  .holder { position: absolute; left: 50px; top: 252px; }
  .holder__name { font-size: 29px; font-weight: 500; color: var(--accent-blue); }
  .holder__creds { font-size: 19px; font-weight: 500; }
  .holder__title { margin-top: 6px; font-size: 20px; font-weight: 300; color: var(--text-grey); }

  .contacts { position: absolute; left: 48px; top: 342px; list-style: none; }
  .contacts li {
    display: flex; align-items: center; gap: 14px;
    height: 33px; font-size: 21px; font-weight: 300; color: var(--text-grey);
  }
  .contacts svg { width: 18px; height: 18px; }
  .contacts .hl { color: var(--accent-blue); }

  .social {
    position: absolute; left: 302px; top: 410px;
    display: flex; align-items: center; gap: 8px;
    font-size: 18px; font-weight: 300; color: var(--accent-blue);
  }
  .social__dot { width: 16px; height: 16px; border-radius: 50%; background: var(--accent-blue); }

  .services {
    position: absolute; left: 548px; top: 180px; list-style: none;
    color: #fff; font-size: 22px; font-weight: 300; line-height: 33px;
  }
  .services li { position: relative; padding-left: 17px; }
  .services li::before {
    content: ""; position: absolute; left: 0; top: 13px;
    width: 9px; height: 9px; border-radius: 50%; background: #fff;
  }
</style>
</head>
<body>
<main class="canvas">

  <section class="card card--front">
    <svg class="art" width="824" height="472" viewBox="0 0 824 472">
      <defs>
        <linearGradient id="faintFlow" x1="0" y1="0" x2="1" y2="0">
          <stop offset="0" stop-color="var(--soft-blue-b)" stop-opacity="0"/>
          <stop offset="1" stop-color="var(--soft-blue-a)"/>
        </linearGradient>
      </defs>
      <ellipse role="img" aria-label="Faint flowing-hair profile illustration" cx="560" cy="230" rx="290" ry="215" fill="url(#faintFlow)"/>
    </svg>

    <div class="wordmark">
      <span class="wordmark__name">MORAVEL</span>
      <span class="wordmark__tag">AESTHETIC DOCTOR</span>
    </div>

    <div class="holder">
      <p class="holder__name">Dr Elise Varnholt, <span class="holder__creds">MRCPCH MD</span></p>
      <p class="holder__title">Australasian Diploma of Aesthetic Medicine</p>
    </div>

    <ul class="contacts">
      <li>
        <svg viewBox="0 0 24 24" fill="var(--accent-blue)"><path d="M6.6 10.8a15 15 0 0 0 6.6 6.6l2.2-2.2c.3-.3.7-.4 1-.2 1.1.4 2.3.6 3.6.6.6 0 1 .4 1 1V20c0 .6-.4 1-1 1A17 17 0 0 1 3 4c0-.6.4-1 1-1h3.5c.6 0 1 .4 1 1 0 1.3.2 2.5.6 3.6.1.3 0 .7-.2 1z"/></svg>
        <span>0800 555 014</span>
      </li>
      <li>
        <svg viewBox="0 0 24 24" fill="none" stroke="var(--accent-blue)" stroke-width="2"><rect x="3" y="5" width="18" height="14" rx="1"/><path d="M3 6l9 7 9-7"/></svg>
        <span>elise@moravel.co.nz</span>
      </li>
      <li>
        <svg viewBox="0 0 24 24" fill="none" stroke="var(--accent-blue)" stroke-width="1.6"><circle cx="12" cy="12" r="9"/><ellipse cx="12" cy="12" rx="4" ry="9"/><path d="M3 12h18M5 7h14M5 17h14"/></svg>
        <span>www.<span class="hl">moravel</span>.co.nz</span>
      </li>
    </ul>

    <div class="social"><span class="social__dot"></span><span>@moravel.clinic</span></div>
  </section>

  <section class="card card--back">
    <svg class="art" width="824" height="472" viewBox="0 0 824 472">
      <defs>
        <linearGradient id="flowBlue" x1="0" y1="0" x2="1" y2="1">
          <stop offset="0" stop-color="#a9dcf4"/>
          <stop offset="0.55" stop-color="#3aa7e2"/>
          <stop offset="1" stop-color="#1f6fb8"/>
        </linearGradient>
      </defs>
      <rect x="0" y="0" width="262" height="472" fill="var(--card-white)"/>
      <circle cx="262" cy="236" r="258" fill="var(--card-white)"/>
      <ellipse role="img" aria-label="Flowing blue hair profile illustration" cx="215" cy="230" rx="215" ry="200" fill="url(#flowBlue)" opacity="0.9"/>
    </svg>

    <div class="wordmark">
      <span class="wordmark__name">MORAVEL</span>
      <span class="wordmark__tag">AESTHETIC DOCTOR</span>
    </div>

    <ul class="services">
      <li>Dermal injectables</li>
      <li>Plasma facials</li>
      <li>Microneedling</li>
      <li>Skin boosters</li>
      <li>Excessive sweating</li>
      <li>Home and Spa Based<br>Treatments</li>
    </ul>
  </section>

</main>
</body>
</html>
```